Delphine's Stone Hearth Trattoria Pitch Deck

Clean and Minimalist Layout: Use a clean and uncluttered layout with ample white space to enhance readability and focus on the key content.

Color Palette: Choose a color scheme that aligns with your brand identity. Black and White. Opt for a combination of complementary colors to create a visually appealing and cohesive look throughout the presentation.

Typography: Select modern and legible fonts for headings and body text. Consider using a combination of serif and sans-serif fonts to create contrast and hierarchy.

High-Quality Images: Incorporate high-resolution images that visually represent your pizzeria, food offerings, and brand. Ensure the images are clear, well-lit, and of professional quality.

Graphs and Charts: Utilize visually appealing graphs and charts to present financial projections, market data, and growth metrics. Choose appropriate chart types, such as bar graphs or line charts, to effectively communicate data.

Iconography: Include relevant icons and symbols to enhance visual interest and provide quick visual cues. Use them to represent different sections, services, or key points in your presentation.

Slide Transitions and Animations: Use subtle slide transitions and animations to add a touch of interactivity and engage your audience. However, avoid overusing flashy animations that may distract from the content.

Consistent Branding: Ensure that your pitch deck maintains consistent branding elements throughout, such as your logo, color scheme, and typography. This helps to reinforce your brand identity and create a cohesive presentation.

Remember, the goal is to create a visually appealing and professional pitch deck that effectively communicates your key messages. Use visuals, graphs, and design elements strategically to enhance understanding and engagement with your audience.

Target Market(s)

Investors

Industry/Entity Type

Food Industry

Font styles to use
Serif

Colors

Designer to choose only greyscale colors for use in the design.

Requirements
Must have
• Modern and Professional Look: Opt for a modern design that reflects the professional nature of your business. Use clean lines, contemporary fonts, and a visually appealing color scheme to create a polished and professional appearance. Consistent Branding: Incorporate your pizzeria's branding elements such as the logo, colors, and typography throughout the pitch deck. Consistency in branding helps to establish a cohesive and memorable visual identity. Visual Hierarchy: Use visual hierarchy to guide the viewer's attention and emphasize important information. Utilize font sizes, colors, and formatting techniques such as bold and italics to differentiate headings, subheadings, and body text. Engaging Visuals: Incorporate relevant and eye-catching visuals such as high-quality images, graphics, and icons. Visuals should support your content and help communicate your message effectively. Well-Structured Layout: Organize your content into sections and use clear headings and subheadings to create a logical flow. Ensure that each slide has enough white space for readability and avoid cluttered designs. Legible Fonts: Choose fonts that are easy to read on both computer screens and projection screens. Stick to a maximum of two font styles to maintain a clean and professional look. Charts and Graphs: When presenting data or statistics, use charts, graphs, and infographics to present information visually. This makes complex information more digestible and visually appealing. Slide Transitions and Animations: Use slide transitions and subtle animations to enhance the visual experience. However, avoid excessive animations that can distract from your content. Balance of Text and Visuals: Strike a balance between text and visuals. Avoid overcrowding slides with excessive text and focus on presenting key points in a concise and visually appealing manner. Relevance to Content: Ensure that the design elements align with and enhance the content of your pitch deck. Avoid using decorative elements that do not serve a purpose or distract from the main message. Remember, the design should complement and support your content rather than overpowering it. A well-designed pitch deck will capture attention, convey professionalism, and enhance the overall impact of your presentation.

```html
<!DOCTYPE html>
<html lang="en">
<head>
<meta charset="utf-8">
<title>Delphine's Stone Hearth Trattoria — Pitch Deck</title>
<link href="https://fonts.googleapis.com/css2?family=DM+Serif+Text&family=DM+Sans:wght@400;600;700&display=swap" rel="stylesheet">
<style>
:root{
  --bg:#e6e7e9;
  --paper:#ffffff;
  --ink:#111111;
  --charcoal:#262626;
  --mute:#444444;
  --rule:#9a9a9a;
  --warm-a:#6b4a32;
  --warm-b:#c98a4a;
  --warm-c:#3a2a20;
}
*{margin:0;padding:0;box-sizing:border-box}
html,body{width:779px;height:1200px;overflow:hidden;background:var(--bg)}
body{position:relative;font-family:'DM Sans',sans-serif;color:var(--ink)}
.slide{position:absolute;width:310px;height:174px;background:var(--paper);overflow:hidden;box-shadow:0 1px 3px rgba(0,0,0,.12)}
.slide.dark{background:var(--charcoal);color:var(--paper)}
.col-l{left:57px}.col-r{left:410px}
.row-1{top:54px}.row-2{top:284px}.row-3{top:514px}.row-4{top:744px}.row-5{top:974px}
.abs{position:absolute}
.serif{font-family:'DM Serif Text',serif}
.brand{position:absolute;display:flex;align-items:center;gap:2px;font-family:'DM Serif Text',serif;font-size:7px;line-height:1;color:var(--ink)}
.brand .dot{width:4px;height:4px;border-radius:50%;background:currentColor}
.dark .brand,.brand.light{color:var(--paper)}
.brand.tr{top:8px;right:8px}
.photo{position:absolute;inset:0}
.pg{position:absolute;right:10px;bottom:6px;font-size:3px;color:var(--mute)}
.dark .pg,.pg.light{color:#ccc}
h2.title{position:absolute;font-family:'DM Serif Text',serif;font-weight:400;font-size:11.5px;line-height:1;color:var(--ink)}
h2.title::after{content:"";display:block;width:36px;height:1px;margin-top:2px;background:currentColor}
.dark h2.title,.title.light{color:var(--paper)}
.body{font-size:4.2px;line-height:1.38;color:var(--ink)}
.dark .body{color:#e9e9e9}

/* cover */
.cover-title{position:absolute;left:17px;top:45px;font-family:'DM Serif Text',serif;font-size:17px;line-height:1.03}
.person{position:absolute;left:17px;font-size:3.4px;line-height:1.35}
.person b{display:block;font-size:5.6px;font-weight:700;margin-bottom:.5px}
.cover-rule{position:absolute;left:17px;top:134px;width:71px;height:.6px;background:var(--rule)}
.dark .cover-rule{background:#5d8a6b}

/* pills */
.pill{position:absolute;display:flex;align-items:center;background:var(--ink);color:var(--paper);border-radius:14px}
.pill .lbl{font-family:'DM Serif Text',serif;font-size:6px;line-height:1.05;padding-left:3px;width:30px}
.pill .txt{font-size:4px;line-height:1.25;border-left:.5px solid #fff;padding-left:3px;margin-left:2px;width:95px}
.ico{display:block;flex:none}

.tab{position:absolute;display:flex;align-items:center;gap:3px;background:var(--ink);color:var(--paper);border-radius:4px;padding:0 4px;font-family:'DM Serif Text',serif;font-size:5.2px;line-height:1.08}
.note{position:absolute;font-size:4px;line-height:1.32}

.band-head{position:absolute;display:flex;align-items:center;gap:4px;background:var(--ink);color:var(--paper);border-radius:3px 3px 0 0;font-family:'DM Serif Text',serif;font-size:6.4px;line-height:1;padding:0 6px}
.sub{font-family:'DM Serif Text',serif;font-size:5.6px;line-height:1.05;margin-bottom:1.5px}
.ribbon{position:absolute;left:0;display:flex;align-items:center;gap:4px;height:15px;background:var(--ink);color:var(--paper);border-radius:0 8px 8px 0;padding:0 6px 0 8px;font-family:'DM Serif Text',serif;font-size:5.4px}
.tagline{position:absolute;left:0;right:0;top:1163px;text-align:center;font-family:'DM Serif Text',serif;font-size:15px;color:var(--ink)}
.ph-circle{position:absolute;left:17px;width:19px;height:19px;border:.6px solid #fff;border-radius:50%;display:flex;align-items:center;justify-content:center;font-size:3px;color:#fff}
</style>
</head>
<body>

<!-- 1 Cover light -->
<section class="slide col-l row-1">
  <div class="photo" role="img" aria-label="Photo of the two owners standing behind a counter of pizzas in front of the stone oven" style="background:linear-gradient(120deg,#8a6d57,#b99a7c 40%,#5a5248 70%,#c58c55);clip-path:path('M150 0 H310 V174 H118 C122 110 132 50 150 0 Z')"></div>
  <svg class="abs" style="left:0;top:0" width="310" height="174" viewBox="0 0 310 174" aria-hidden="true"><path d="M150 0 C132 50 122 110 118 174" fill="none" stroke="#111" stroke-width="5"/></svg>
  <div class="brand" style="left:17px;top:16px;font-size:9px"><span class="dot"></span>Delphine's</div>
  <h1 class="cover-title">Delphine's<br>Stone Hearth<br>Trattoria</h1>
  <div class="person" style="top:112px"><b>Marco Ferrante</b>(Owner &amp; CEO)<br>marco@delphinestrattoria.com</div>
  <div class="cover-rule"></div>
  <div class="person" style="top:142px"><b>Luca Brennan</b>(Owner, Silent Partner)<br>luca@delphinestrattoria.com</div>
</section>

<!-- 2 Cover dark -->
<section class="slide dark col-r row-1">
  <div class="photo" role="img" aria-label="Photo of the two owners standing behind a counter of pizzas in front of the stone oven" style="background:linear-gradient(120deg,#8a6d57,#b99a7c 40%,#5a5248 70%,#c58c55);clip-path:path('M150 0 H310 V174 H118 C122 110 132 50 150 0 Z')"></div>
  <svg class="abs" style="left:0;top:0" width="310" height="174" viewBox="0 0 310 174" aria-hidden="true"><path d="M150 0 C132 50 122 110 118 174" fill="none" stroke="#f2f2f2" stroke-width="4"/></svg>
  <div class="brand" style="left:17px;top:16px;font-size:9px"><span class="dot"></span>Delphine's</div>
  <h1 class="cover-title">Delphine's<br>Stone Hearth<br>Trattoria</h1>
  <div class="person" style="top:112px"><b>Marco Ferrante</b>(Owner &amp; CEO)<br>marco@delphinestrattoria.com</div>
  <div class="cover-rule"></div>
  <div class="person" style="top:142px"><b>Luca Brennan</b>(Owner, Silent Partner)<br>luca@delphinestrattoria.com</div>
</section>

<!-- 3 Introduction -->
<section class="slide col-l row-2">
  <div class="photo" role="img" aria-label="Photo of the restaurant storefront with its illuminated sign" style="background:linear-gradient(160deg,#d9cfc2,#b6a896 45%,#7d8a7e 75%,#3f5d4c);clip-path:polygon(0 0,150px 0,205px 100%,0 100%)"></div>
  <div class="brand tr"><span class="dot"></span>Delphine's</div>
  <h2 class="title" style="left:189px;top:19px">Introduction</h2>
  <p class="body abs" style="left:189px;top:37px;width:112px;font-size:4.5px"><b>Delphine's Stone Hearth Trattoria</b> is a quality casual restaurant offering freshly cooked, delicious pizzas made with carefully crafted homemade sauce and dough. We prioritize customer satisfaction and provide lightning-quick food times, making us a top choice for takeout and delivery.</p>
  <div class="pill" style="left:155px;top:99px;width:145px;height:30px">
    <svg class="ico" width="14" height="14" viewBox="0 0 14 14" style="margin-left:5px"><path d="M2 7 Q7 2 12 7 Q7 12 2 7Z" fill="none" stroke="#fff" stroke-width=".7"/><circle cx="7" cy="7" r="1.6" fill="#fff"/></svg>
    <span class="lbl"><span style="font-size:4.5px">Our</span><br>Vision</span>
    <span class="txt">to become the go-to destination for exceptional pizza experiences, known for our quality ingredients and outstanding service.</span>
  </div>
  <div class="pill" style="left:155px;top:133px;width:145px;height:30px">
    <svg class="ico" width="14" height="14" viewBox="0 0 14 14" style="margin-left:5px"><circle cx="7" cy="7" r="5" fill="none" stroke="#fff" stroke-width=".7"/><circle cx="7" cy="7" r="2.5" fill="none" stroke="#fff" stroke-width=".7"/><path d="M7 7 L12 2" stroke="#fff" stroke-width=".7"/></svg>
    <span class="lbl"><span style="font-size:4.5px">Our</span><br>Mission</span>
    <span class="txt">to delight customers with every bite and create memorable moments through our delicious pizzas.</span>
  </div>
  <span class="pg">3</span>
</section>

<!-- 4 Market -->
<section class="slide col-r row-2">
  <div class="photo" role="img" aria-label="Photo of a pizza baking in the flames of a brick oven" style="background:linear-gradient(200deg,#f0a040,#c4601c 35%,#5b2a12 70%,#2a160c);clip-path:polygon(241px 0,100% 0,100% 100%,170px 100%)"></div>
  <div class="brand tr light"><span class="dot"></span>Delphine's</div>
  <h2 class="title" style="left:10px;top:22px">The Market Opportunity</h2>
  <div class="tab" style="left:10px;top:42px;width:64px;height:34px">
    <svg class="ico" width="9" height="9" viewBox="0 0 10 10"><circle cx="4" cy="4" r="3" fill="none" stroke="#fff" stroke-width=".7"/><path d="M6 6 L9 9" stroke="#fff" stroke-width=".8"/></svg>Overview of the Pizza Industry</div>
  <p class="note" style="left:79px;top:44px;width:122px">The pizza industry is a thriving and highly popular segment of the food service market. With a diverse range of customers and a growing demand for convenient dining options, the pizza industry presents significant growth opportunities.</p>
  <div class="tab" style="left:10px;top:82px;width:64px;height:34px">
    <svg class="ico" width="9" height="9" viewBox="0 0 10 10"><path d="M1 9 V5 H3 V9 M4 9 V3 H6 V9 M7 9 V1 H9 V9" fill="none" stroke="#fff" stroke-width=".6"/></svg>Market Size and Growth Potential</div>
  <p class="note" style="left:79px;top:81px;width:116px">The pizza industry generates billions of dollars in revenue each year, and its potential for growth remains strong. As we expand our presence, we tap into the market's appetite for quality pizza options and capitalize on the increasing trend of takeout and delivery services.</p>
  <div class="tab" style="left:10px;top:123px;width:64px;height:34px">
    <svg class="ico" width="9" height="9" viewBox="0 0 10 10"><circle cx="5" cy="3" r="1.5" fill="#fff"/><circle cx="2" cy="6" r="1.2" fill="#fff"/><circle cx="8" cy="6" r="1.2" fill="#fff"/><path d="M3 9 Q5 5 7 9" fill="#fff"/></svg>Target Audience and Customer Demographics</div>
  <p class="note" style="left:79px;top:122px;width:98px">Our target audience encompasses a wide range of individuals from 18 to 80 years old, both male and female, with a focus on the middle-class demographic. By offering a menu that caters to diverse tastes and preferences, we can attract a broad customer base.</p>
  <span class="pg light">4</span>
</section>

<!-- 5 USP -->
<section class="slide col-l row-3">
  <div class="abs" style="left:0;top:0;width:310px;height:57px;background:var(--ink)"></div>
  <div class="abs" role="img" aria-label="Photo of a baked pizza with greens" style="left:90px;top:8px;width:72px;height:72px;border-radius:50%;background:radial-gradient(circle,#e0a458,#b5652c 60%,#6b3b1e)"></div>
  <div class="abs" role="img" aria-label="Photo of a white pizza with eggs" style="left:163px;top:-10px;width:65px;height:48px;border-radius:50%;background:radial-gradient(circle,#f0d7a3,#d09a54 60%,#7a5633)"></div>
  <div class="abs" role="img" aria-label="Photo of a pepperoni pizza" style="left:222px;top:30px;width:70px;height:70px;border-radius:50%;background:radial-gradient(circle,#d88646,#b04c22 60%,#6a2e17)"></div>
  <div class="brand tr light"><span class="dot"></span>Delphine's</div>
  <h2 class="title light" style="left:10px;top:14px;font-size:12px;line-height:1.05">Unique Selling<br>Proposition</h2>
  <div class="band-head" style="left:10px;top:64px;width:141px;height:23px">
    <svg class="ico" width="12" height="12" viewBox="0 0 12 12"><circle cx="6" cy="6" r="5" fill="none" stroke="#fff" stroke-width=".7"/><path d="M6 6 L6 1 M6 6 L10 8 M6 6 L2 8" stroke="#fff" stroke-width=".6"/></svg>What Sets<br>Our Pizzeria Apart</div>
  <p class="body abs" style="left:10px;top:91px;width:141px;font-size:4.6px">At Delphine's Stone Hearth Trattoria, our commitment to excellence sets us apart. We pride ourselves on using carefully crafted proprietary recipes for our homemade sauce and dough, resulting in exceptional product quality. Our small, profitable menu ensures consistency and allows us to deliver lightning-quick food times, making us a customer favorite.</p>
  <div class="band-head" style="left:159px;top:64px;width:141px;height:23px">
    <svg class="ico" width="12" height="12" viewBox="0 0 12 12"><circle cx="6" cy="2.5" r="1.5" fill="none" stroke="#fff" stroke-width=".6"/><path d="M1 11 V7 H4 V11 M4.5 11 V5 H7.5 V11 M8 11 V8 H11 V11" fill="none" stroke="#fff" stroke-width=".6"/></svg>Key Differentiators<br>and Competitive Advantages</div>
  <p class="body abs" style="left:159px;top:91px;width:141px;font-size:4.6px">Our ability to make anything on our menu in a matter of minutes, coupled with our convenient ordering options, including mobile ordering, delivery service, takeout, and in-person dining, sets us apart from the competition. We prioritize meeting our customers' exact fast-paced needs and providing the best quality product and service.</p>
  <span class="pg">5</span>
</section>

<!-- 6 Business Model -->
<section class="slide col-r row-3">
  <div class="photo" role="img" aria-label="Photo of the chef's hands placing a pizza on a wooden counter" style="background:linear-gradient(150deg,#e9e6e2,#b9b0a6 40%,#c79a68 70%,#8a5a33);clip-path:polygon(0 0,110px 0,158px 100%,0 100%)"></div>
  <div class="brand tr"><span class="dot"></span>Delphine's</div>
  <h2 class="title" style="left:149px;top:20px">Business Model</h2>
  <div class="tab" style="left:79px;top:37px;width:64px;height:34px">
    <svg class="ico" width="10" height="10" viewBox="0 0 10 10"><rect x="1" y="2" width="8" height="6" fill="none" stroke="#fff" stroke-width=".6"/><circle cx="5" cy="5" r="1.4" fill="none" stroke="#fff" stroke-width=".6"/></svg>Revenue<br>Streams</div>
  <p class="note" style="left:149px;top:41px;width:136px">Our revenue streams include dine-in, takeout, delivery, and catering services. By offering multiple avenues for customers to enjoy our pizzas, we maximize revenue opportunities and cater to various preferences.</p>
  <div class="tab" style="left:91px;top:79px;width:64px;height:34px">
    <svg class="ico" width="10" height="10" viewBox="0 0 10 10"><rect x="2" y="1" width="6" height="8" fill="none" stroke="#fff" stroke-width=".6"/><path d="M3.5 3.5 H6.5 M3.5 5 H6.5 M3.5 6.5 H6.5" stroke="#fff" stroke-width=".5"/></svg>Pricing<br>Strategy and<br>Menu Overview</div>
  <p class="note" style="left:161px;top:82px;width:142px">We have meticulously priced our menu to ensure maximum profitability while delivering value to our customers. Our menu offers a carefully selected range of signature pies, including the Rosa, Verde, and Classic pies, ensuring that each pizza is a delightful experience for our customers.</p>
  <div class="tab" style="left:103px;top:120px;width:64px;height:34px">
    <svg class="ico" width="10" height="10" viewBox="0 0 10 10"><circle cx="5" cy="5" r="4" fill="none" stroke="#fff" stroke-width=".6"/><path d="M5 2.5 V5 H7" fill="none" stroke="#fff" stroke-width=".6"/></svg>Operating Hours<br>and Location(s)</div>
  <p class="note" style="left:173px;top:124px;width:128px">Our pizzeria operates from 11 am to 9 pm, allowing us to cater to lunch and dinner crowds. Our flagship location is situated at 18 Harbor Lane, Suite 4, Milford, DE 19963, providing a convenient and accessible location for customers.</p>
  <span class="pg">6</span>
</section>

<!-- 7 Growth -->
<section class="slide col-l row-4">
  <div class="photo" role="img" aria-label="Faded photo of a chef stretching pizza dough" style="background:linear-gradient(160deg,#f4f2ef,#e6ddd2 50%,#ddc7a8);opacity:.85"></div>
  <div class="brand tr"><span class="dot"></span>Delphine's</div>
  <h2 class="title" style="left:10px;top:22px">Growth Strategy</h2>
  <svg class="abs" style="left:0;top:0" width="310" height="174" viewBox="0 0 310 174" aria-hidden="true">
    <path d="M26 118 C60 80 150 52 248 42 L243 18 L283 40 L252 74 L250 56 C160 64 80 86 26 118Z" fill="#111"/>
    <circle cx="87" cy="84" r="14" fill="#fff" stroke="#111" stroke-width="1.2"/>
    <path d="M87 77 a3 3 0 0 1 3 3 c0 2.5 -3 5.5 -3 5.5 s-3 -3 -3 -5.5 a3 3 0 0 1 3 -3Z M80 92 L94 92 L91 87 L83 87Z" fill="none" stroke="#111" stroke-width=".7"/>
    <circle cx="202" cy="53" r="17" fill="#fff" stroke="#111" stroke-width="1.2"/>
    <rect x="195" y="47" width="14" height="11" fill="none" stroke="#111" stroke-width=".7"/><path d="M197 55 L201 51 L204 54 L207 49" fill="none" stroke="#111" stroke-width=".7"/>
  </svg>
  <div class="abs" style="left:75px;top:102px;width:106px">
    <p class="sub">Expansion Plans and<br>Potential Locations</p>
    <p class="body" style="font-size:4.1px">Our growth strategy involves establishing a strong foothold in Delaware with 5 locations. Once we have built a solid foundation, we plan to expand into Philadelphia, New Jersey, New York, Connecticut, and Boston, aiming for 5-10 locations per state. This strategic expansion will allow us to capture a wider market and achieve economies of scale.</p>
  </div>
  <div class="abs" style="left:189px;top:76px;width:100px">
    <p class="sub">Marketing and<br>Advertising Strategies</p>
    <p class="body" style="font-size:4.1px">Our marketing approach focuses on organic marketing through social media platforms, leveraging user-generated content and online reviews to build brand recognition and engage with our target audience. Additionally, we collaborate with third-party marketing applications such as QuickDish, RideEats, and FeastHub to extend our reach and attract new customers.</p>
  </div>
  <span class="pg">7</span>
</section>

<!-- 8 Financial -->
<section class="slide col-r row-4">
  <div class="abs" style="left:227px;top:0;width:83px;height:174px;background:var(--ink)"></div>
  <div class="abs" role="img" aria-label="Photo of a pizza partly visible at the top edge" style="left:150px;top:-40px;width:56px;height:52px;border-radius:50%;background:radial-gradient(circle,#d88646,#a6542a 60%,#5c3018)"></div>
  <div class="abs" role="img" aria-label="Photo of a pizza partly visible at the bottom edge" style="left:215px;top:150px;width:46px;height:46px;border-radius:50%;background:radial-gradient(circle,#d88646,#a6542a 60%,#5c3018)"></div>
  <div class="brand tr light"><span class="dot"></span>Delphine's</div>
  <h2 class="title" style="left:10px;top:27px">Financial Projections</h2>
  <div class="ribbon" style="top:46px;width:106px">
    <svg class="ico" width="9" height="9" viewBox="0 0 10 10"><circle cx="5" cy="3" r="2" fill="none" stroke="#fff" stroke-width=".6"/><path d="M1 9.5 Q5 4 9 9.5Z" fill="none" stroke="#fff" stroke-width=".6"/></svg>Sales and Revenue Forecast</div>
  <p class="note" style="left:20px;top:65px;width:205px;font-size:4.6px">Based on historical sales data and our growth strategy, we project continued growth for the next three years. In 2022, our first full year of operation, our sales reached $265,697.20. In 2023, we expect sales to increase to $425,946.56, and in 2024, we forecast sales to reach $700,000.</p>
  <div class="ribbon" style="top:100px;width:173px">
    <svg class="ico" width="9" height="9" viewBox="0 0 10 10"><circle cx="5" cy="3.5" r="2.2" fill="none" stroke="#fff" stroke-width=".6"/><path d="M1 8 H9 M2 9.5 H8" stroke="#fff" stroke-width=".6"/></svg>Revenue Expectations for 5 Locations in Delaware</div>
  <p class="note" style="left:20px;top:120px;width:195px;font-size:4.6px">With our expansion plan to establish 5 locations in Delaware, we anticipate a significant boost in revenue. Based on market analysis and the success of our flagship location, we estimate that these 5 locations combined can generate annual sales of approximately $3 million. This revenue projection takes into account the demand for quality pizza options in the area and our ability to capture a significant market share.</p>
  <div class="abs" style="left:219px;top:45px;width:75px;height:11px;background:#777;clip-path:polygon(0 0,88% 0,100% 100%,0 100%);color:#fff;font-family:'DM Serif Text',serif;font-size:5.4px;display:flex;align-items:center;gap:3px;padding-left:4px">
    <svg class="ico" width="7" height="7" viewBox="0 0 10 10"><circle cx="5" cy="5" r="4" fill="none" stroke="#fff" stroke-width=".8"/><path d="M5 5 V1 M5 5 H9" stroke="#fff" stroke-width=".8"/></svg>Profit Margins</div>
  <p class="note" style="left:236px;top:61px;width:70px;color:#eee;font-size:5px">Our business model is designed to achieve industry-high profit margins of 18%. By carefully managing our cost structure, optimizing operational efficiencies, and leveraging economies of scale as we expand, we are confident in our ability to maintain healthy profit margins across all locations.</p>
  <span class="pg light">8</span>
</section>

<!-- 9 Investment -->
<section class="slide col-l row-5">
  <div class="brand tr"><span class="dot"></span>Delphine's</div>
  <h2 class="title" style="left:10px;top:27px">Investment Opportunity</h2>
  <svg class="abs" style="left:0;top:0" width="310" height="174" viewBox="0 0 310 174" role="img" aria-label="Pie graphic split into three photo wedges of pizza">
    <path d="M156 83 L156 51 A32 32 0 0 1 184 99Z" fill="#d39a5c" stroke="#fff" stroke-width="1.2"/>
    <path d="M156 83 L184 99 A32 32 0 0 1 128 99Z" fill="#6e6a4a" stroke="#fff" stroke-width="1.2"/>
    <path d="M156 83 L128 99 A32 32 0 0 1 156 51Z" fill="#e2b57a" stroke="#fff" stroke-width="1.2"/>
    <g fill="#111"><circle cx="125" cy="70" r="8"/><circle cx="188" cy="70" r="8"/><circle cx="155" cy="119" r="8"/></g>
    <g fill="none" stroke="#fff" stroke-width=".6">
      <circle cx="125" cy="68" r="2"/><path d="M121 74 H129 M122 72 L128 72"/>
      <rect x="184" y="66" width="8" height="7"/><path d="M186 71 L188 68 L190 70"/>
      <path d="M151 123 V119 M154 123 V116 M157 123 V118 M160 123 V115 M150 123 H161"/>
    </g>
  </svg>
  <div class="abs" style="left:18px;top:54px;width:92px;text-align:right">
    <p class="sub" style="font-size:5.2px">Funding Requirements<br>and Use of Funds</p>
    <p class="body" style="font-size:4.3px">To support our expansion plans and achieve our growth targets, we are seeking an investment of $2 million. The funds will be used for new location build-outs, equipment purchases, marketing and advertising campaigns, operational reserves, and working capital.</p>
  </div>
  <div class="abs" style="left:201px;top:54px;width:98px">
    <p class="sub" style="font-size:5.2px">Proposed Investment<br>Structure and Terms</p>
    <p class="body" style="font-size:4.3px">The investment structure and terms will be negotiated based on the investment amount and the level of involvement desired by the investor. We are committed to ensuring a mutually beneficial partnership that aligns with our long-term growth plans.</p>
  </div>
  <div class="abs" style="left:60px;top:136px;width:190px;text-align:center">
    <p class="sub" style="font-size:5.2px;margin-bottom:1px">Equity or Debt Investment Options</p>
    <p class="body" style="font-size:4.3px">We are open to both equity and debt investment options. We can discuss the terms and conditions based on the investor's preferences and our mutual goals.</p>
  </div>
  <span class="pg">9</span>
</section>

<!-- 10 Thank You -->
<section class="slide dark col-r row-5">
  <div class="photo" role="img" aria-label="Photo of a ball of pizza dough on a floured wooden board" style="background:linear-gradient(150deg,#5a4434,#8a6a52 30%,#ddd5cb 55%,#c9beb2 75%,#4e3a2c);clip-path:polygon(172px 0,100% 0,100% 100%,133px 100%)"></div>
  <div class="brand tr light"><span class="dot"></span>Delphine's</div>
  <h2 class="title light" style="left:17px;top:18px;font-size:14px">Thank You</h2>
  <p class="body abs" style="left:17px;top:55px;width:130px;font-size:4.4px">Delphine's Stone Hearth Trattoria presents an exciting investment opportunity in the thriving pizza industry. With our unique selling proposition, strong growth strategy, and experienced management team, we are well-positioned to expand and build out Delphine's to 50-100 locations.</p>
  <div class="ph-circle" style="top:118px">PHOTO</div>
  <div class="person" style="left:42px;top:112px"><b>Marco Ferrante</b>(Owner &amp; CEO)<br>marco@delphinestrattoria.com</div>
  <div class="abs" style="left:42px;top:135px;width:71px;height:.5px;background:#888"></div>
  <div class="ph-circle" style="top:146px">PHOTO</div>
  <div class="person" style="left:42px;top:142px"><b>Luca Brennan</b>(Owner, Silent Partner)<br>luca@delphinestrattoria.com</div>
</section>

<p class="tagline">and many more slide</p>
</body>
</html>
```